Health supplement brand needs a new logo for flagship product launch

I have attached a Word document to the brief which gives more detail.

There are 3 different products that we will sell. The label should be interchangeable across all 3 products, where only the colours change. This requires both a selection of a font typface to match our style and a new image embedded in the logo.

Target Market(s)

The target customer is women aged between 25 and 60. We would like to cross over between both audiences, without ruling one out

Font styles to use
Sans Serif

Requirements
Must have
• - It must be eye catching, i.e. people need to stop scrolling when they see it.
- It must have contemporary colours that are popular with women, i.e. pinks, apricots, dark greens, mustards, etc
- The image needs to be very feminine, just like the target audience
- The label must evoke some emotion, yet still be a little bit fun without being too serious.
- The label must use this image below as the main foundation. I have included the EPS file with this email.
Nice to have
• - We want to be somewhere in the middle, as in, the right price point accessible for most people, but still with a bit of class, fun and femininity
Should not have
• - We also don’t want it to look like “just another” nutritional brand selling Crestwyn Blends

```html
<!DOCTYPE html>
<html lang="en">
<head>
<meta charset="utf-8">
<title>Solvia Bloom – Label Range</title>
<link rel="stylesheet" href="https://fonts.googleapis.com/css2?family=Montserrat:wght@300;400;500;600&display=swap">
<style>
  :root {
    --ink: #1a1a1a;
    --paper: #ffffff;
    --page: #ffffff;
    --brand: #1f1f1f;
    --benefit: #e8c560;
    --blush: #f1ddd2;
    --brand-dot: #7fcab2;
  }
  * { box-sizing: border-box; margin: 0; padding: 0; }
  html, body {
    width: 1200px; height: 1200px; overflow: hidden;
    background: var(--page);
    font-family: "Montserrat", sans-serif;
    color: var(--ink);
  }
  .range {
    position: absolute; left: 10px; top: 385px;
    display: flex; gap: 20px;
  }
  .label {
    position: relative;
    width: 380px; height: 430px;
    background: var(--paper);
    border: 1px solid #444;
    overflow: hidden;
  }
  .label--renew   { --accent: #e2bd55; }
  .label--calm    { --accent: #b7967b; }
  .label--balance { --accent: #efb4a8; }

  .brand {
    position: absolute; top: 30px; left: 0; right: 0;
    display: flex; justify-content: center; align-items: center; gap: 10px;
  }
  .brand__name {
    font-weight: 300; font-size: 26px; letter-spacing: 7px;
    color: var(--brand); text-transform: uppercase; white-space: nowrap;
  }
  .brand__dot {
    width: 10px; height: 10px; border-radius: 50%;
    background: var(--brand-dot);
  }
  .figure-art {
    position: absolute; left: 18px; top: 94px;
    width: 102px; height: 186px;
    border-radius: 48% 52% 30% 40% / 30% 30% 20% 20%;
    background: linear-gradient(180deg, #f6e6dc 0%, var(--blush) 60%, #e6d2c6 100%);
  }
  .product-line {
    position: absolute; left: 128px; top: 124px;
    font-weight: 400; font-size: 21px; white-space: nowrap;
  }
  .product-name {
    position: absolute; left: 156px; top: 158px;
    font-weight: 600; font-size: 32px; letter-spacing: 1px;
    line-height: 1;
    color: var(--accent); white-space: nowrap;
  }
  .descriptor {
    position: absolute; right: 16px; top: 198px;
    font-weight: 400; font-size: 11px; white-space: nowrap;
  }
  .benefits {
    position: absolute; right: 16px; top: 218px;
    font-weight: 300; font-size: 14px; color: var(--benefit); white-space: nowrap;
  }
  .meadow-art {
    position: absolute; left: 0; bottom: 0;
    width: 380px; height: 190px;
  }
</style>
</head>
<body>
<main class="range">

  <section class="label label--renew">
    <div class="brand"><span class="brand__name">Solvia Bloom</span><span class="brand__dot"></span></div>
    <div class="figure-art" role="img" aria-label="Line illustration of a seated woman seen from behind"></div>
    <p class="product-line">Gut Fiber Blend</p>
    <h2 class="product-name">RENEW</h2>
    <p class="descriptor">Neutral taste, pure daily peptide blend</p>
    <p class="benefits">Hair | Skin|Nails | Joints |Muscles</p>
    <svg class="meadow-art" viewBox="0 0 380 190" role="img" aria-label="Abstract brush-stroke meadow with line-drawn flower and dandelions in mustard, blush and taupe">
      <defs>
        <linearGradient id="meadow-renew" x1="0" x2="1" y1="0" y2="0">
          <stop offset="0" stop-color="#e9c464"/>
          <stop offset="0.2" stop-color="#d6a13a"/>
          <stop offset="0.45" stop-color="#efb3a6"/>
          <stop offset="0.65" stop-color="#b5907a"/>
          <stop offset="1" stop-color="#e9c464"/>
        </linearGradient>
      </defs>
      <path d="M0 45 H210 C240 30 250 15 300 10 C340 6 370 20 380 35 V190 H0 Z" fill="url(#meadow-renew)"/>
    </svg>
  </section>

  <section class="label label--calm">
    <div class="brand"><span class="brand__name">Solvia Bloom</span><span class="brand__dot"></span></div>
    <div class="figure-art" role="img" aria-label="Line illustration of a seated woman seen from behind"></div>
    <p class="product-line">PEPTIDES</p>
    <h2 class="product-name">CALM GLOW</h2>
    <p class="descriptor">Neutral taste, pure daily peptide blend</p>
    <p class="benefits">Hair | Skin|Nails | Joints |Muscles</p>
    <svg class="meadow-art" viewBox="0 0 380 190" role="img" aria-label="Abstract brush-stroke meadow with line-drawn flower and dandelions in taupe, apricot, yellow and blush">
      <defs>
        <linearGradient id="meadow-calm" x1="0" x2="1" y1="0" y2="0">
          <stop offset="0" stop-color="#ecb68c"/>
          <stop offset="0.3" stop-color="#b08c70"/>
          <stop offset="0.5" stop-color="#ebc038"/>
          <stop offset="0.75" stop-color="#efb8ad"/>
          <stop offset="1" stop-color="#b08c70"/>
        </linearGradient>
      </defs>
      <path d="M0 45 H210 C240 30 250 15 300 10 C340 6 370 20 380 35 V190 H0 Z" fill="url(#meadow-calm)"/>
    </svg>
  </section>

  <section class="label label--balance">
    <div class="brand"><span class="brand__name">Solvia Bloom</span><span class="brand__dot"></span></div>
    <div class="figure-art" role="img" aria-label="Line illustration of a seated woman seen from behind"></div>
    <p class="product-line">Gut PEPTIDES</p>
    <h2 class="product-name">BALANCE</h2>
    <p class="descriptor">Neutral taste, pure daily peptide blend</p>
    <p class="benefits">Hair | Skin|Nails | Joints |Muscles</p>
    <svg class="meadow-art" viewBox="0 0 380 190" role="img" aria-label="Abstract brush-stroke meadow with line-drawn flower and dandelions in pink, blush, yellow and taupe">
      <defs>
        <linearGradient id="meadow-balance" x1="0" x2="1" y1="0" y2="0">
          <stop offset="0" stop-color="#f6c8c1"/>
          <stop offset="0.2" stop-color="#f49ca5"/>
          <stop offset="0.45" stop-color="#f6c8c1"/>
          <stop offset="0.6" stop-color="#ebc038"/>
          <stop offset="0.75" stop-color="#b5907a"/>
          <stop offset="1" stop-color="#f6c8c1"/>
        </linearGradient>
      </defs>
      <path d="M0 45 H210 C240 30 250 15 300 10 C340 6 370 20 380 35 V190 H0 Z" fill="url(#meadow-balance)"/>
    </svg>
  </section>

</main>
</body>
</html>
```